KTWG application splash screen

We need a 1024x768 image for use as an application splash screen.
The image will be displayed full screen on an 10 inch industrial PC 1024x768 screen while our application is launching. The image should convey that the application is "Waiting for connection to Wi-Fi access point..." and include a graphic of the industrial PC connected to the access point via an Ethernet cable. A list of troubleshooting steps should be included at the bottom of the image. The troubleshooting steps should not be the main focus of the image and should be shown in a smaller font (but still readable at 1024x768 displayed on a 10 inch screen).
I will include a mock up of the general idea of what we are looking for as well as image files for the industrial PC, a screenshot of our application to show on the PC's screen and the AP.
For general look and feel and a sense of corporate branding please review our website https://marrowgatesoilworks.example/. The splash screen should reflect corporate branding.
Target Market(s)
Users of our application
Industry/Entity Type
Agriculture
Look and feel

```html
<!DOCTYPE html>
<html lang="en">
<head>
<meta charset="utf-8">
<title>KTWG – Waiting for connection</title>
<link rel="stylesheet" href="https://fonts.googleapis.com/css2?family=Archivo:wdth,wght@125,900&family=Poppins:wght@400;500;600;700&display=swap">
<style>
  :root {
    --stage: #999999;
    --brand-green: #43bd6c;
    --panel-dark: #1f1f1f;
    --ink: #111111;
    --white: #ffffff;
    --warn-yellow: #fcdc6c;
    --device-dark: #2a2a2a;
    --device-screen: #e9eeea;
    --ap-white: #f1f2f2;
    --signal-red: #d6371f;
    --icon-grey: #3c3c3c;
  }
  * { box-sizing: border-box; margin: 0; padding: 0; }
  html, body { width: 1200px; height: 1200px; overflow: hidden; }
  body { background: var(--stage); position: relative; font-family: "Poppins", sans-serif; }

  .splash {
    position: absolute; left: 99px; top: 225px;
    width: 1001px; height: 750px;
    background: var(--brand-green);
    overflow: hidden;
  }
  .brand-pennant { position: absolute; left: 60px; top: 0; width: 178px; height: 153px; }
  .brand-name {
    position: absolute; left: 60px; top: 42px; width: 178px;
    display: flex; align-items: center; justify-content: center; gap: 8px;
    font-family: "Archivo", sans-serif; font-stretch: 125%; font-weight: 900;
    font-size: 36px; color: var(--ink); letter-spacing: 1px;
  }
  .brand-dot { width: 16px; height: 16px; border-radius: 50%; background: var(--brand-green); }

  .headline {
    position: absolute; left: 271px; top: 40px;
    font-family: "Archivo", sans-serif; font-stretch: 125%; font-weight: 900;
    font-size: 45px; line-height: 54px; letter-spacing: 0.5px; white-space: nowrap;
  }
  .headline .line-light { color: var(--white); display: block; }
  .headline .line-dark { color: var(--ink); display: block; }

  .device-label {
    position: absolute; color: var(--white); font-weight: 500;
    font-size: 21px; line-height: 27px;
  }
  .device-label--pc { right: 826px; top: 229px; text-align: right; }
  .device-label--ap { left: 825px; top: 229px; }
  .ap-model { position: absolute; left: 825px; top: 316px; color: var(--white); font-size: 11.5px; line-height: 14px; font-family: Arial, sans-serif; }

  .pc-visual {
    position: absolute; left: 202px; top: 201px; width: 194px; height: 153px;
    border-radius: 12px; background: var(--device-dark); padding: 14px 18px 22px;
  }
  .pc-visual span { display: block; width: 100%; height: 100%; background: var(--device-screen); border-radius: 2px; }
  .ap-visual {
    position: absolute; left: 792px; top: 210px; width: 17px; height: 133px;
    border-radius: 6px; background: linear-gradient(90deg, #dcdede, var(--ap-white), #d5d7d7);
  }

  .diagram { position: absolute; left: 0; top: 0; width: 1001px; height: 400px; }

  .cable-label { position: absolute; left: 466px; top: 341px; width: 200px; text-align: center; color: var(--white); font-weight: 500; font-size: 19px; }

  .help-title { position: absolute; left: 0; top: 412px; width: 1001px; text-align: center; font-weight: 700; font-size: 29px; color: var(--ink); padding-left: 0; }
  .help-note { position: absolute; left: 0; top: 452px; width: 1001px; text-align: center; font-size: 13.5px; color: var(--white); }

  .help-panel { position: absolute; left: 0; top: 481px; width: 1001px; height: 269px; background: var(--panel-dark); }
  .help-lead { position: absolute; left: 0; top: 24px; width: 1001px; text-align: center; color: var(--white); font-weight: 600; font-size: 18.5px; }

  .steps { list-style: none; position: absolute; top: 85px; width: 350px; color: var(--white); font-size: 14.5px; line-height: 18px; }
  .steps--left { left: 87px; }
  .steps--right { left: 588px; width: 330px; }
  .steps li { position: relative; padding-left: 18px; margin-bottom: 14px; }
  .steps li svg { position: absolute; left: 0; top: 3px; width: 11px; height: 11px; }

  .tools-icon { position: absolute; left: 464px; top: 85px; width: 110px; height: 110px; }
</style>
</head>
<body>
<main class="splash">
  <svg class="brand-pennant" viewBox="0 0 178 153" aria-hidden="true">
    <polygon points="0,0 178,0 178,123 89,153 0,123" fill="#ffffff"/>
  </svg>
  <div class="brand-name"><span>KTWG</span><span class="brand-dot"></span></div>

  <h1 class="headline">
    <span class="line-light">WAITING FOR CONNECTION</span>
    <span class="line-dark">TO WI-FI ACCESS POINT...</span>
  </h1>

  <p class="device-label device-label--pc">Tractor<br>cab<br>computer</p>
  <div class="pc-visual" role="img" aria-label="Industrial tractor cab computer showing the seeding application"><span></span></div>

  <svg class="diagram" viewBox="0 0 1001 400" aria-hidden="true">
    <polygon points="564,179 656,328 473,328" fill="var(--warn-yellow)"/>
    <rect x="555" y="225" width="19" height="58" fill="var(--ink)"/>
    <rect x="555" y="294" width="19" height="19" fill="var(--ink)"/>
    <path d="M298 359 V378 H801 V353" fill="none" stroke="#e6f5ea" stroke-width="3" stroke-dasharray="8 6"/>
    <g fill="none" stroke="var(--signal-red)" stroke-width="1.8" stroke-linecap="round">
      <path d="M839 230 a13 13 0 0 1 18 0"/>
      <path d="M842 234 a8 8 0 0 1 12 0"/>
    </g>
    <circle cx="848" cy="238" r="1.8" fill="var(--signal-red)"/>
  </svg>

  <p class="cable-label">Ethernet cable</p>

  <div class="ap-visual" role="img" aria-label="Outdoor Wi-Fi access point with antennas"></div>
  <p class="device-label device-label--ap">Wi-Fi<br>Access<br>Point</p>
  <p class="ap-model">Nordlane<br>AX-40 Outdoor</p>

  <h2 class="help-title">Troubleshooting steps</h2>
  <p class="help-note">This screen should only be visible for a short time on boot</p>

  <section class="help-panel">
    <p class="help-lead">If this screen stays visible for more than a</p>

    <ul class="steps steps--left">
      <li><svg viewBox="0 0 12 12"><circle cx="6" cy="6" r="6" fill="var(--brand-green)"/><path d="M3.3 6.2 5.2 8 8.7 4.3" fill="none" stroke="#1f1f1f" stroke-width="1.6"/></svg>Verify that the Wi-Fi Access Point (AP) powers up when this system does (indicated by a green light on the side of the AP).</li>
      <li><svg viewBox="0 0 12 12"><circle cx="6" cy="6" r="6" fill="var(--brand-green)"/><path d="M3.3 6.2 5.2 8 8.7 4.3" fill="none" stroke="#1f1f1f" stroke-width="1.6"/></svg>Check the Ethernet cable between this system and the AP for damage, and replace it if necessary.</li>
    </ul>

    <svg class="tools-icon" viewBox="0 0 110 110" aria-hidden="true">
      <g fill="none" stroke="var(--icon-grey)" stroke-width="6" stroke-linejoin="round" stroke-linecap="round">
        <path d="M47 8 h16 l3 12 10 5 11-6 11 11-6 11 4 10 12 3 v16 l-12 3 -4 10 6 11 -11 11 -11-6 -10 4 -3 12 h-16 l-3-12 -10-4 -11 6 -11-11 6-11 -4-10 -12-3 v-16 l12-3 4-10 -6-11 11-11 11 6 10-5z"/>
        <path d="M40 40 a15 15 0 0 0 18 20 l22 22 a6 6 0 0 0 8-8 l-22-22 a15 15 0 0 0 -20-18 l10 10 -6 6z"/>
      </g>
    </svg>

    <ul class="steps steps--right">
      <li><svg viewBox="0 0 12 12"><circle cx="6" cy="6" r="6" fill="var(--brand-green)"/><path d="M3.3 6.2 5.2 8 8.7 4.3" fill="none" stroke="#1f1f1f" stroke-width="1.6"/></svg>Power-cycle this system and wait for it to reboot fully.</li>
      <li style="margin-top:34px"><svg viewBox="0 0 12 12"><circle cx="6" cy="6" r="6" fill="var(--brand-green)"/><path d="M3.3 6.2 5.2 8 8.7 4.3" fill="none" stroke="#1f1f1f" stroke-width="1.6"/></svg>If the issue persists, contact KTWG support for further assistance.</li>
    </ul>
  </section>
</main>
</body>
</html>
```